Create a proposal + product powerpoint

Please see the powerpoint for the slides. There are about 20 slides to be created. Rest of them are for reference and show the design that I like.

I would like to move fast on this, since I need to present it next week (in the week of April 21st).

Please download the current content from here:
https://www.parcelbrook.net/fetch/qRtVmXzLwPkNbYcD

Please make at least 4 slides with the specific content so I can assess your design style.

Target Market(s)

Business Audience and very senior technical audience
Decision Makers

Industry/Entity Type

Product

Colors
e34297
a64599

Requirements
Must have
• Should be very clean, crisp.

I like to use Icons as shown in the powerpoint.... Please see the appendix of the slide deck that shows the various icons. Most of them just have plain text, and I would like to organize so that it does not look like some is just reading text.

I would like to focus on the design aspects so that the audience is clear on how the solution works.

Every page should some graphic element based on the slides shown in the appendix.

```html
<!DOCTYPE html>
<html lang="en">
<head>
<meta charset="utf-8">
<title>Time spent on non-development activities</title>
<link rel="stylesheet" href="https://fonts.googleapis.com/css2?family=Roboto+Condensed:wght@300;400;700&display=swap">
<style>
  :root {
    --title: #a8179d;
    --label: #8e1f73;
    --muted: #9a9a9a;
    --rule: #d6d6d6;
    --axis: #f08fe0;
    --dev-a: #a83c98;
    --dev-b: #cc3cb8;
    --integrate: #de6bcb;
    --troubleshoot: #f48ce4;
    --release: #fabdf1;
    --footer: #9b1d5b;
    --footer-accent: #a64599;
    --bg: #ffffff;
  }
  * { box-sizing: border-box; margin: 0; padding: 0; }
  html, body { width: 1200px; height: 900px; overflow: hidden; background: var(--bg); }
  body { font-family: "Roboto Condensed", "Arial Narrow", sans-serif; }
  .slide {
    position: relative; width: 1200px; height: 900px; overflow: hidden;
    background:
      radial-gradient(ellipse 260px 300px at 0 760px, rgba(200, 120, 210, 0.35), rgba(255,255,255,0) 100%),
      var(--bg);
  }
  .slide-title {
    position: absolute; left: 38px; top: 22px;
    font-size: 39px; font-weight: 400; color: var(--title); letter-spacing: -0.2px;
  }
  .title-rule { position: absolute; left: 42px; top: 91px; width: 1113px; height: 2px; background: var(--rule); }
  .brand-box {
    position: absolute; left: 1035px; top: 12px; width: 150px; height: 66px;
    border: 2px solid #e4e4e4; border-radius: 8px; background: #fff;
    display: flex; align-items: center; justify-content: center;
    font-size: 28px; font-weight: 300; color: #9a9a9a; letter-spacing: 1px;
  }
  .backdrop { position: absolute; left: 0; top: 96px; }
  .legend { position: absolute; right: 330px; top: 141px; list-style: none; }
  .legend li {
    display: flex; align-items: center; justify-content: flex-end;
    height: 33px; margin-bottom: 14px;
    font-size: 21px; font-weight: 300; color: var(--muted);
  }
  .legend .swatch { width: 40px; height: 33px; margin-left: 12px; }
  .dev { background: linear-gradient(160deg, var(--dev-a), var(--dev-b)); }
  .integrate { background: var(--integrate); }
  .troubleshoot { background: var(--troubleshoot); }
  .release { background: var(--release); }
  .chart { position: absolute; left: 0; top: 0; }
  .bar { position: absolute; left: 197px; height: 61px; display: flex; }
  .bar span { height: 100%; }
  .bar-platform { top: 438px; }
  .bar-legacy { top: 576px; }
  .pct { position: absolute; font-size: 25px; font-weight: 300; color: var(--muted); transform: translateX(-50%); }
  .category {
    position: absolute; right: 1038px; text-align: center;
    font-size: 27px; font-weight: 400; color: var(--label); line-height: 36px;
  }
  .footer { position: absolute; left: 0; top: 840px; }
  .footer-text { position: absolute; top: 855px; font-size: 23px; font-weight: 400; color: #fff; }
  .page-no { left: 14px; }
  .copyright { right: 14px; }
</style>
</head>
<body>
<main class="slide">
  <svg class="backdrop" width="1200" height="744" viewBox="0 0 1200 744" role="img" aria-label="Decorative faceted triangle pattern in soft magenta tones">
    <defs>
      <linearGradient id="facets" x1="0" y1="0" x2="1" y2="0">
        <stop offset="0" stop-color="#f6d8f1" stop-opacity="0"/>
        <stop offset="0.3" stop-color="#eeb7e6"/>
        <stop offset="1" stop-color="#cc5dc9"/>
      </linearGradient>
    </defs>
    <polygon points="930,0 1200,0 1200,744 920,744 1000,560 880,380 1000,200" fill="url(#facets)" opacity="0.85"/>
  </svg>

  <h1 class="slide-title">Disproportionate time is spent on non-development activities</h1>
  <div class="title-rule"></div>
  <div class="brand-box">LOGO HERE</div>

  <ul class="legend">
    <li>Development<span class="swatch dev"></span></li>
    <li>Integrating code<span class="swatch integrate"></span></li>
    <li>Troubleshooting<span class="swatch troubleshoot"></span></li>
    <li>Release Management<span class="swatch release"></span></li>
  </ul>

  <svg class="chart" width="1200" height="900" viewBox="0 0 1200 900" aria-hidden="true">
    <g stroke="var(--axis)" stroke-width="4" fill="none" stroke-linecap="round" stroke-linejoin="round">
      <line x1="180" y1="250" x2="180" y2="702"/>
      <polyline points="166,264 180,248 194,264"/>
      <line x1="180" y1="702" x2="920" y2="702"/>
      <polyline points="906,688 922,702 906,716"/>
    </g>
  </svg>

  <p class="category" style="top:435px;">Nimbus.io</p>
  <p class="category" style="top:570px;">Legacy<br>Platform</p>

  <div class="bar bar-platform">
    <span class="dev" style="width:117px"></span>
    <span class="integrate" style="width:183px"></span>
    <span class="troubleshoot" style="width:183px"></span>
    <span class="release" style="width:184px"></span>
  </div>
  <span class="pct" style="left:258px; top:510px;">10%</span>
  <span class="pct" style="left:405px; top:510px;">30%</span>
  <span class="pct" style="left:588px; top:510px;">30%</span>
  <span class="pct" style="left:780px; top:510px;">30%</span>

  <div class="bar bar-legacy">
    <span class="dev" style="width:267px"></span>
    <span class="integrate" style="width:133px"></span>
    <span class="troubleshoot" style="width:134px"></span>
    <span class="release" style="width:133px"></span>
  </div>
  <span class="pct" style="left:330px; top:646px;">70%</span>
  <span class="pct" style="left:528px; top:646px;">10%</span>
  <span class="pct" style="left:663px; top:646px;">10%</span>
  <span class="pct" style="left:795px; top:646px;">10%</span>

  <svg class="footer" width="1200" height="60" viewBox="0 0 1200 60" aria-hidden="true">
    <rect x="0" y="0" width="1200" height="60" fill="var(--footer)"/>
    <polygon points="905,0 925,0 955,60 935,60" fill="#ffffff"/>
    <polygon points="925,0 1200,0 1200,60 955,60" fill="var(--footer-accent)"/>
  </svg>
  <span class="footer-text page-no">Page : 01</span>
  <span class="footer-text copyright">Copyright text here</span>
</main>
</body>
</html>
```